Envelope Design - Winner can do follow-up business

- Varnoko.com is a Swiss-based online store selling business shirts and accessories for business men
- Please visit the webpage to make yourself familiar with the company. Although the text is in German, with Plimbo translator you should be able to understand the main content.
- Our clients are mainly business men between 30 and 60 years old. Mostly with a high income working in the service industry (banking, insurance, lawyers, etc.). Sometimes there wives purchase the shirts for them ;-)
- The colors and the logo are given, as they are also used for the print materials (please see files in attachment)
- I am running several businesses and often need a talented web designer --> the winner gets substantial follow-up business
your task:
-for our company we need a new envelope design
-It should be simple and modern
-please use one of the logos in the followings.
-suprise me :)

```html
<!DOCTYPE html>
<html lang="en">
<head>
<meta charset="utf-8">
<title>Varnoko envelope set</title>
<link rel="stylesheet" href="https://fonts.googleapis.com/css2?family=Open+Sans:wght@400;600&display=swap">
<style>
  :root {
    --backdrop: #e7e4df;
    --paper: #ffffff;
    --paper-edge: #9a9a9a;
    --brand-red: #ee2e24;
    --brand-red-soft: #f47a62;
    --brand-yellow: #e8d86a;
    --brand-grey: #86857a;
    --ink-white: #ffffff;
  }
  html, body {
    margin: 0;
    padding: 0;
    width: 1200px;
    height: 962px;
    overflow: hidden;
    background: var(--backdrop);
  }
  .envelope-set {
    display: block;
    width: 1200px;
    height: 962px;
  }
  .paper { fill: var(--paper); }
  .paper-outlined { fill: var(--paper); stroke: var(--paper-edge); stroke-width: 1; }
  .flap-red, .band-red { fill: var(--brand-red); }
  .flap-yellow, .swoosh-yellow { fill: var(--brand-yellow); }
  .brand-name {
    font-family: "Open Sans", sans-serif;
    font-weight: 600;
  }
  .brand-name--flap-red { fill: var(--brand-red-soft); }
  .brand-name--flap-yellow { fill: var(--brand-grey); }
  .brand-name--front { fill: var(--brand-yellow); }
  .brand-square { fill: var(--brand-yellow); }
  .contact-line {
    font-family: "Open Sans", sans-serif;
    font-weight: 400;
    font-size: 20px;
    fill: var(--ink-white);
  }
  .icon-stroke { fill: none; stroke: var(--ink-white); stroke-width: 1.8; }
  .icon-fill { fill: var(--ink-white); }
</style>
</head>
<body>
<svg class="envelope-set" viewBox="0 0 1200 962" xmlns="http://www.w3.org/2000/svg">

  <!-- Back envelope with red flap -->
  <g class="envelope envelope--back">
    <rect class="paper" x="153" y="62" width="981" height="462"/>
    <path class="flap-red" d="M153 62 H1135 C1126 102 1114 128 1074 136 L670 211 Q645 217 620 211 L214 136 C176 128 166 102 158 62 Z"/>
    <text class="brand-name brand-name--flap-red" x="645" y="165" font-size="28" text-anchor="middle" letter-spacing="3">VARNOKO</text>
  </g>

  <!-- Middle envelope with yellow flap -->
  <g class="envelope envelope--middle">
    <rect class="paper-outlined" x="60.5" y="252.5" width="982" height="462"/>
    <path class="flap-yellow" d="M61 253 H1042 C1034 292 1020 320 980 328 L590 403 Q565 409 540 403 L138 328 C98 320 82 292 61 253 Z"/>
    <text class="brand-name brand-name--flap-yellow" x="550" y="346" font-size="46" text-anchor="middle" textLength="274" lengthAdjust="spacingAndGlyphs">VARNOKO</text>
  </g>

  <!-- Front envelope -->
  <g class="envelope envelope--front">
    <rect class="paper-outlined" x="137.5" y="436.5" width="982" height="462"/>

    <g class="brand-lockup">
      <rect class="brand-square" x="281" y="467" width="50" height="50"/>
      <text class="brand-name brand-name--front" x="166" y="580" font-size="48" textLength="277" lengthAdjust="spacingAndGlyphs">VARNOKO</text>
    </g>

    <path class="swoosh-yellow" d="M138 806 C420 768 770 776 1120 843 L1120 864 C770 800 420 790 138 812 Z"/>
    <path class="band-red" d="M138 817 C420 796 770 804 1120 870 V899 H138 Z"/>

    <g class="contact">
      <g class="icon icon--globe" transform="translate(177 838)">
        <circle class="icon-stroke" r="9.5"/>
        <ellipse class="icon-stroke" rx="4.2" ry="9.5"/>
        <line class="icon-stroke" x1="-9.5" y1="0" x2="9.5" y2="0"/>
        <line class="icon-stroke" x1="-8" y1="-4.8" x2="8" y2="-4.8"/>
        <line class="icon-stroke" x1="-8" y1="4.8" x2="8" y2="4.8"/>
      </g>
      <text class="contact-line" x="200" y="845">www.varnoko.com</text>

      <g class="icon icon--pin" transform="translate(175 873)">
        <path class="icon-fill" d="M0 12 C-6 4 -9 0 -9 -4 A9 9 0 0 1 9 -4 C9 0 6 4 0 12 Z M0 -8 A3.6 3.6 0 1 0 0.01 -8 Z" fill-rule="evenodd"/>
      </g>
      <text class="contact-line" x="200" y="880">Street Name, City Name, State Zipcode</text>
    </g>
  </g>
</svg>
</body>
</html>
```